Managed IT services business card design

We haven't needed a business card since the founding of the business in 2005. All our clients have been coming through word of mouth. And lately more and more existing clients are requesting for our business cards to pass on to their contacts in recommending us.
So we needing a business card design. We use various innovative solutions and methodologies to provide IT services to small businesses in managing their IT systems. Our role is the same as an in-house, full-time IT Manager for our clients, but outsourced. So we take care of all our clients' IT needs, just as an IT Manager would be expected to perform.
We have a holding website, which we're happy to leave for now. If we can use the same logo would be great - www.lumadesk.com.au
Preferred colours are shades of are white, grey and black.
We pride our business with the following traits: proactive, good service, prompt response, trustworthy.
Target Market(s)
Small businesses of any industry
Industry/Entity Type
Business

```html
<!DOCTYPE html>
<html lang="en">
<head>
<meta charset="utf-8">
<title>Lumadesk business card</title>
<link rel="stylesheet" href="https://fonts.googleapis.com/css2?family=Montserrat:wght@400&family=Open+Sans:wght@400&display=swap">
<style>
  :root {
    --backdrop: #e6e6e6;
    --card: #575c60;
    --ink: #ffffff;
    --tab-text: #2b2e30;
    --shadow: rgba(0, 0, 0, 0.22);
  }
  * { margin: 0; padding: 0; box-sizing: border-box; }
  html, body {
    width: 1200px; height: 680px; overflow: hidden;
    background: var(--backdrop);
  }
  .sheet {
    position: relative; width: 1200px; height: 680px;
    display: flex; align-items: center; justify-content: center; gap: 60px;
  }
  .card {
    position: relative; width: 520px; height: 300px;
    background: var(--card); color: var(--ink);
    box-shadow: 0 6px 18px var(--shadow);
    overflow: hidden;
  }
  .wordmark {
    position: absolute;
    font-family: "Montserrat", sans-serif; font-weight: 400;
    letter-spacing: 0.32em; color: var(--ink);
    display: flex; align-items: center; gap: 14px;
  }
  .wordmark-dot { width: 10px; height: 10px; background: var(--ink); }
  .card-front .wordmark { left: 118px; top: 112px; font-size: 42px; }
  .card-back .wordmark { left: 40px; top: 78px; font-size: 30px; }
  .card-back .wordmark-dot { width: 8px; height: 8px; }

  .url-tab {
    position: absolute; background: var(--ink); color: var(--tab-text);
    font-family: "Open Sans", sans-serif; font-size: 12px; letter-spacing: 0.24em;
    display: flex; align-items: center; justify-content: center; white-space: nowrap;
  }
  .card-front .url-tab {
    right: 0; bottom: 0; width: 270px; height: 40px;
    border-top-left-radius: 22px;
  }
  .card-back .url-tab {
    right: 0; top: 0; width: 40px; height: 200px;
    border-bottom-left-radius: 22px;
  }
  .card-back .url-tab span { transform: rotate(90deg); }

  .person {
    position: absolute; left: 44px; top: 146px;
    font-family: "Open Sans", sans-serif;
  }
  .person-name { font-size: 17px; line-height: 1.1; }
  .person-role { font-size: 13px; padding-left: 12px; }

  .contacts {
    position: absolute; left: 56px; top: 212px; list-style: none;
    font-family: "Open Sans", sans-serif; font-size: 15px; line-height: 20px;
  }
  .contacts li { display: flex; align-items: center; gap: 8px; }
  .contacts svg { width: 14px; height: 14px; flex: none; }

  .address {
    position: absolute; right: 64px; top: 170px; text-align: right;
    font-family: "Open Sans", sans-serif; font-size: 14px; line-height: 18px;
  }
</style>
</head>
<body>
<main class="sheet">
  <section class="card card-front" aria-label="Card front">
    <div class="wordmark">lumadesk<span class="wordmark-dot"></span></div>
    <div class="url-tab"><span>www.lumadesk.com.au</span></div>
  </section>

  <section class="card card-back" aria-label="Card back">
    <div class="wordmark">lumadesk<span class="wordmark-dot"></span></div>
    <div class="url-tab"><span>www.lumadesk.com.au</span></div>

    <div class="person">
      <p class="person-name">Mark Ellison</p>
      <p class="person-role">director</p>
    </div>

    <ul class="contacts">
      <li>
        <svg viewBox="0 0 16 16" aria-hidden="true"><circle cx="8" cy="8" r="7" fill="none" stroke="#fff" stroke-width="1.4"/><path d="M5.5 4.5c0 4 2 6 6 6l-0.5-1.8-1.6 0.4-2.4-2.4 0.4-1.6z" fill="#fff"/></svg>
        512 555 0140
      </li>
      <li>
        <svg viewBox="0 0 16 16" aria-hidden="true"><rect x="4" y="2" width="8" height="5" fill="none" stroke="#fff" stroke-width="1.3"/><rect x="1.5" y="7" width="13" height="7" rx="1" fill="#fff"/></svg>
        512 555 0141
      </li>
      <li>
        <svg viewBox="0 0 16 16" aria-hidden="true"><rect x="1.5" y="3.5" width="13" height="9" fill="#fff"/><path d="M1.5 3.5l6.5 5 6.5-5" fill="none" stroke="#575c60" stroke-width="1.3"/></svg>
        info@lumadesk.com.au
      </li>
    </ul>

    <address class="address" style="font-style:normal">
      1480 Alder Creek Rd<br>
      Marlow TX 78010
    </address>
  </section>
</main>
</body>
</html>
```